Ice Cream Product Packaging - Bucket and Lid

We need some high quality packaging designed for a client who manufactures and sells 'healthy' Ice Cream (low calories, high protein etc).
The logo needs to be designed also which is the main image of the packaging.
Prefer lower case for main fonts. needs to look elegant, naughty and high end.
There are 2 flavours at this stage - chocolate and vanilla.
Target market is for adults - 18-40, fitness, gym etc.

There are 2 sizes but let's just get the largest one sorted first?

Title: "lumen" (means 'kiss' in French) - they want an image of some pronounced red lips behind the name. The red lips will be their main brand identity/logo.. With some chocolate dripping out of the side. (brown for the chocolate flavour and a cream colour for the vanilla flavour). Maybe a faded image of an attactive womans face - mainly the lips and chin (if chin is necessary?!) - the text "Ice Creamery" can be in a small font underneath

Subtitle: Can go above (or below) main title: "naughty & healthy" followed on the next line by: "Low Calories + High Protein" (they are thinking about spelling 'naughty' incorrectly - like "nauty".. I'm not sure about this though..what do you think?!) This text can be in gold or silver perhaps and a handwriting font to give it that high end look? Up to you.

Background - whatever you think.. some sort of nice textured background perhaps? brown shades for the chocolate flavour, creamy/yellowy shades for the vanilla flavour. Can we also have some ice cream 'dripping' from the top.

There will be a section of 6 lips icons that will say: Gluten Free, High Protein, Low Calories, Lactose Free, No Added Sugar, Digestive Enzyme. These icons can go down the side of the bucket.

Colours: Red, black, brown (for choc), cream (for vanilla), gold and/or silver, white or cream etc etc.
Bucket for chocolate will be black so there is a black lip at the top (tamper proof seal). Bucket for Vanilla is white so will be white at the top - tamper proof seal. incorporate those colurs.

We also need some room for ingredients text, barcode and some company info.

Please see the files attachedfor a rough version. Doesn't need to be exactly the same but something similar would be fantastic.

Also attached are the 2 ice cream bucket sizes, their dimensions and the Lid size.
Lid will just be a copy of the main image on the bucket.

Target Market(s)

adults, 18-40, fitness, healthy, gym, foodies

Font styles to use
Sans Serif
Script

Colors
ec1f27
f04a50
fff3d1
ffffff
1b1b1b

Requirements
Must have
• Elegant look, high end, healthy ice cream, red lips... see description for more detailed info
Nice to have
• see description for more detailed info
Should not have

```html
<!DOCTYPE html>
<html lang="en">
<head>
<meta charset="utf-8">
<title>lumen chocolate tub label</title>
<link rel="stylesheet" href="https://fonts.googleapis.com/css2?family=Rubik:wght@500;700;800&family=Poppins:wght@300;400&family=Allura&display=swap">
<style>
  :root {
    --cream: #f6ead6;
    --cream-light: #fbf2e3;
    --choc: #5a2b22;
    --choc-dark: #3a1712;
    --red: #ec1f27;
    --red-script: #e0394a;
    --ink: #1b1b1b;
    --white: #ffffff;
  }
  * { margin: 0; padding: 0; box-sizing: border-box; }
  html, body { width: 1200px; height: 1200px; overflow: hidden; background: var(--white); }
  .label {
    position: absolute; left: 14px; top: 382px;
    width: 1172px; height: 436px;
    background: var(--cream); overflow: hidden;
    font-family: "Poppins", sans-serif; color: var(--ink);
  }
  .abs { position: absolute; }
  .center { transform: translateX(-50%); white-space: nowrap; text-align: center; }

  .base-band { left: 0; top: 392px; width: 1172px; height: 44px; background: var(--choc); }
  .benefit-panel { left: 928px; top: 0; width: 244px; height: 392px; background: var(--cream-light); }
  .flavour-rule { left: 0; top: 263px; width: 744px; height: 4px; background: var(--choc); }
  .flavour-pill {
    left: 484px; top: 250px; width: 168px; height: 30px; border-radius: 15px;
    background: var(--choc); color: var(--cream);
    font-family: "Rubik", sans-serif; font-weight: 800; font-size: 26px; line-height: 30px;
  }

  .nutrition { left: 28px; top: 32px; width: 190px; height: 165px; border: 2px solid var(--ink); background: var(--white); }
  .nutrition h3 { font-family: "Rubik", sans-serif; font-weight: 700; font-size: 19px; line-height: 24px; padding-left: 4px; border-bottom: 2px solid var(--ink); }
  .nutrition .row { border-bottom: 1px solid var(--ink); height: 8px; }
  .nutrition .row.thick { border-bottom-width: 2px; }
  .nutrition .row.tall { height: 38px; }

  .drip { left: 268px; top: 0; width: 80px; height: 134px; background: var(--choc-dark); border-radius: 0 0 36px 36px; }

  .claims { left: 482px; top: 45px; font-family: "Rubik", sans-serif; font-weight: 700; font-size: 14px; }
  .tagline { left: 482px; top: 64px; font-family: "Allura", cursive; font-size: 28px; color: var(--red-script); }
  .subbrand { left: 482px; top: 100px; font-weight: 300; font-size: 26px; }
  .wordmark { left: 366px; top: 124px; font-weight: 300; font-size: 96px; line-height: 1; letter-spacing: 1px; color: var(--ink); white-space: nowrap; }

  .why { left: 838px; top: 16px; font-size: 26px; line-height: 30px; color: var(--choc); }

  .benefit { left: 1050px; font-family: "Rubik", sans-serif; font-weight: 700; font-size: 22px; line-height: 26px; }
  .benefit::before { content: ""; display: inline-block; width: 10px; height: 10px; border-radius: 50%; background: var(--red); margin-right: 8px; vertical-align: middle; }

  .ingredients { left: 744px; top: 262px; width: 184px; height: 130px; background: var(--choc); color: var(--white); padding: 13px 0 0 26px; }
  .ingredients h4 { font-family: "Rubik", sans-serif; font-weight: 700; font-size: 14px; line-height: 18px; }
  .ingredients p { font-size: 9.5px; line-height: 12px; margin-top: 3px; width: 150px; }
  .ingredients .rule { width: 126px; height: 2px; background: var(--white); margin-top: 4px; }
  .ingredients .keep { font-family: "Allura", cursive; font-size: 24px; line-height: 28px; }
</style>
</head>
<body>
<main class="label">
  <div class="abs benefit-panel"></div>
  <div class="abs base-band"></div>

  <div class="abs nutrition">
    <h3>Nutrition Facts</h3>
    <div class="row"></div>
    <div class="row thick"></div>
    <div class="row"></div>
    <div class="row"></div>
    <div class="row"></div>
    <div class="row"></div>
    <div class="row tall thick"></div>
    <div class="row"></div>
  </div>

  <div class="abs drip" role="img" aria-label="Melted chocolate dripping from the top edge"></div>

  <div class="abs center claims">Low Calories &nbsp;+&nbsp; High Protein</div>
  <div class="abs center tagline">Nauty &amp; Healthy</div>
  <div class="abs center subbrand">ice creamery</div>
  <div class="abs wordmark">lumen</div>

  <div class="abs flavour-rule"></div>
  <div class="abs center flavour-pill">chocolate</div>

  <div class="abs center why">Why choose<br>lumen?</div>

  <div class="abs center benefit" style="top:23px">Gluten Free</div>
  <div class="abs center benefit" style="top:88px">High Protein</div>
  <div class="abs center benefit" style="top:151px">Low Calories</div>
  <div class="abs center benefit" style="top:216px">Lactose Free</div>
  <div class="abs center benefit" style="top:281px">No Added Sugar</div>
  <div class="abs center benefit" style="top:342px">Digestive Enzyme</div>

  <section class="abs ingredients">
    <h4>Ingredients</h4>
    <p>Low fat milk, sugar, salt cacao extract, vanilla, non-dairy creamer</p>
    <div class="rule"></div>
    <div class="keep">Keep Frozen</div>
  </section>
</main>
</body>
</html>
```